Sparrow Haulage needs a business card design.

Design a double-sided business card for new freight business. On the front, would like to see our logo along with the following info:

Martin Obuya
CEO/FOUNDER
555-206-7142
martinobuya@sparrow-haulage.example

On the reverse side, we would like to use the graphic image of our logo only without the Sparrow Haulage name.

```html
<!DOCTYPE html>
<html lang="en">
<head>
<meta charset="utf-8">
<title>Sparrow Haulage — Business Card</title>
<link rel="stylesheet" href="https://fonts.googleapis.com/css2?family=Arimo:wght@400;700&display=swap">
<style>
  :root {
    --backdrop: #2b2b2d;
    --card: #0d0d0e;
    --card-edge: #1a1a1c;
    --navy: #1c1f8c;
    --red: #c8151b;
    --white: #f1f1f1;
    --silver: #d9d9db;
    --rule: #3a3a3d;
  }
  * { box-sizing: border-box; margin: 0; padding: 0; }
  html, body {
    width: 1200px; height: 900px; overflow: hidden;
    background: var(--backdrop);
    font-family: "Arimo", Arial, sans-serif;
  }
  .canvas {
    position: relative; width: 1200px; height: 900px;
    display: flex; flex-direction: column; align-items: center; justify-content: center;
    gap: 60px;
  }
  .card {
    position: relative; width: 620px; height: 354px;
    background: var(--card);
    border: 1px solid var(--card-edge);
    border-radius: 22px;
    overflow: hidden;
  }
  /* front */
  .brand {
    position: absolute; left: 40px; bottom: 70px;
    display: flex; align-items: center; gap: 12px;
  }
  .brand-mark { width: 18px; height: 18px; background: var(--red); flex: none; }
  .brand-name {
    font-weight: 700; font-size: 21px; line-height: 22px; letter-spacing: 0.12em;
    color: var(--red); text-transform: uppercase;
  }
  .brand-name span { display: block; }
  .divider {
    position: absolute; left: 256px; top: 92px; width: 1px; height: 170px;
    background: var(--rule);
  }
  .details { position: absolute; left: 278px; top: 94px; white-space: nowrap; }
  .person-name { font-weight: 700; font-size: 25px; letter-spacing: 0.02em; text-transform: uppercase; }
  .person-name .first { color: var(--navy); }
  .person-name .last { color: var(--red); }
  .person-title { margin-top: 4px; font-size: 19px; color: var(--white); }
  .contacts { margin-top: 30px; list-style: none; }
  .contacts li {
    display: flex; align-items: center; gap: 9px;
    font-size: 15px; color: var(--white); line-height: 24px;
  }
  .contacts svg { width: 15px; height: 15px; flex: none; }
  /* back */
  .card-back { display: flex; align-items: center; justify-content: center; }
  .back-mark { width: 120px; height: 120px; border-radius: 50%; background: var(--silver); }
</style>
</head>
<body>
<main class="canvas">
  <section class="card card-front" aria-label="Business card front">
    <div class="brand">
      <span class="brand-mark"></span>
      <span class="brand-name"><span>Sparrow</span><span>Haulage</span></span>
    </div>
    <div class="divider"></div>
    <div class="details">
      <h1 class="person-name"><span class="first">Martin</span> <span class="last">Obuya</span></h1>
      <p class="person-title">CEO/FOUNDER</p>
      <ul class="contacts">
        <li>
          <svg viewBox="0 0 16 16" aria-hidden="true"><path fill="var(--red)" d="M3.6 1.2l2.3 2.6-1.3 1.7c.9 2 2.7 3.9 4.8 4.9l1.7-1.3 2.6 2.3-1.4 2.3C7.4 13.6 2.4 8.6 1.3 3z"/></svg>
          555-206-7142
        </li>
        <li>
          <svg viewBox="0 0 16 16" aria-hidden="true"><rect x="1" y="3" width="14" height="10" fill="var(--red)"/><path d="M1 3l7 6 7-6" fill="none" stroke="var(--card)" stroke-width="1.3"/></svg>
          martinobuya@sparrow-haulage.example
        </li>
        <li>
          <svg viewBox="0 0 16 16" aria-hidden="true"><circle cx="8" cy="8" r="7" fill="var(--red)"/><g fill="none" stroke="var(--card)" stroke-width="1"><ellipse cx="8" cy="8" rx="3" ry="7"/><path d="M1 8h14M2.2 4.5h11.6M2.2 11.5h11.6"/></g></svg>
          www.sparrow-haulage.example
        </li>
      </ul>
    </div>
  </section>

  <section class="card card-back" aria-label="Business card back">
    <div class="back-mark" role="img" aria-label="Company symbol in silver"></div>
  </section>
</main>
</body>
</html>
```